Stylish new business card needed!

Hello everyone! I am in need of a new business card design for an alarm company here in Hurricane WV. I have all fonts, color codes and logos provided for you use! We are a young company and like the style of a clean sleek looking business card. Would like it double sided, one side holding the logo and the other with your design!
Target Market(s)
The people that are looking for the newest tech for home automation and security
Industry/Entity Type
Alarm services; Home automation
Contact Information for Business Card
Name of person; position (Sales; Installer); Phone Number (555.418.7260); Employee cell Number; Website (www.GuardedByVelk.example); Employee Email; Double sided
Look and feel
Each slider illustrates characteristics of the customer's brand and the style your logo design should communicate.

```html
<!DOCTYPE html>
<html lang="en">
<head>
<meta charset="utf-8">
<title>Velk Business Card – Double Sided</title>
<link rel="stylesheet" href="https://fonts.googleapis.com/css2?family=Archivo+Black&family=Arimo:wght@400;700&display=swap">
<style>
  :root {
    --page-bg: #18181b;
    --card-bg: #232227;
    --card-edge: #f18a3d;
    --accent: #f18a3d;
    --grey: #9a9a9c;
    --white: #f4f4f4;
    --emboss: #1b1a1e;
    --emboss-hi: #2c2b31;
  }
  * { box-sizing: border-box; margin: 0; padding: 0; }
  html, body { width: 1200px; height: 780px; overflow: hidden; }
  body {
    background: var(--page-bg);
    display: flex;
    flex-direction: column;
    align-items: center;
    justify-content: center;
    gap: 28px;
    font-family: "Arimo", Arial, sans-serif;
  }
  .card {
    position: relative;
    width: 620px;
    height: 354px;
    background: var(--card-bg);
    border-radius: 22px;
    border-bottom: 3px solid var(--card-edge);
    border-left: 2px solid var(--card-edge);
    overflow: hidden;
    box-shadow: 0 18px 40px rgba(0,0,0,0.55);
  }

  /* Logo side */
  .card-back .brand-lockup {
    position: absolute;
    inset: 0;
    display: flex;
    flex-direction: column;
    align-items: center;
    justify-content: center;
  }
  .card-back .brand-kicker,
  .card-back .brand-name,
  .card-back .brand-tagline {
    font-family: "Archivo Black", "Arial Black", sans-serif;
    color: var(--emboss);
    text-shadow: 1px 1px 0 var(--emboss-hi);
    white-space: nowrap;
  }
  .card-back .brand-kicker { font-size: 26px; letter-spacing: 1px; line-height: 1; }
  .card-back .brand-name { font-size: 110px; letter-spacing: 2px; line-height: 1.05; }
  .card-back .brand-tagline { font-size: 12px; letter-spacing: 1px; margin-top: 6px; }

  /* Detail side */
  .accent-tab {
    position: absolute;
    top: 0; right: 70px;
    width: 22px; height: 44px;
    background: var(--accent);
  }
  .person {
    position: absolute;
    top: 40px; right: 104px;
    text-align: right;
  }
  .person-name {
    font-family: "Archivo Black", "Arial Black", sans-serif;
    font-size: 28px;
    line-height: 1.05;
    white-space: nowrap;
  }
  .person-name .first { color: var(--accent); }
  .person-name .last { color: var(--grey); }
  .person-role {
    font-weight: 700;
    font-size: 15px;
    color: var(--white);
    margin-top: 4px;
  }
  .brand-block {
    position: absolute;
    left: 42px; top: 62px;
    font-family: "Archivo Black", "Arial Black", sans-serif;
    color: var(--accent);
    white-space: nowrap;
  }
  .brand-block .brand-kicker { font-size: 17px; line-height: 1; letter-spacing: 0.5px; }
  .brand-block .brand-name {
    font-size: 52px;
    line-height: 1.05;
    display: flex;
    align-items: center;
    gap: 10px;
  }
  .brand-block .brand-dot {
    width: 14px; height: 14px;
    border-radius: 50%;
    background: var(--accent);
  }
  .brand-block .brand-tagline {
    font-size: 9px;
    letter-spacing: 0.8px;
    margin-top: 2px;
  }
  .watermark-name {
    position: absolute;
    right: 24px; bottom: 60px;
    font-family: "Archivo Black", "Arial Black", sans-serif;
    font-size: 96px;
    line-height: 1;
    color: var(--emboss);
    text-shadow: 1px 1px 0 var(--emboss-hi);
  }
  .contacts {
    position: absolute;
    left: 42px; bottom: 30px;
    list-style: none;
    display: flex;
    flex-direction: column;
    gap: 6px;
  }
  .contacts li {
    display: flex;
    align-items: center;
    gap: 10px;
    font-size: 15px;
    color: var(--white);
    white-space: nowrap;
  }
  .contacts svg { width: 15px; height: 15px; flex: none; }
</style>
</head>
<body>

  <section class="card card-back" aria-label="Card logo side">
    <div class="brand-lockup">
      <div class="brand-kicker">GUARDED BY</div>
      <div class="brand-name">VELK</div>
      <div class="brand-tagline">AUTOMATION AND SECURITY SERVICES</div>
    </div>
  </section>

  <section class="card card-front" aria-label="Card contact side">
    <div class="accent-tab"></div>

    <div class="brand-block">
      <div class="brand-kicker">GUARDED BY</div>
      <div class="brand-name"><span class="brand-dot"></span>VELK</div>
      <div class="brand-tagline">AUTOMATION AND SECURITY SERVICES</div>
    </div>

    <div class="person">
      <div class="person-name"><span class="first">Mara</span> <span class="last">Lindqvist</span></div>
      <div class="person-role">Sales; Installer</div>
    </div>

    <div class="watermark-name">VELK</div>

    <ul class="contacts">
      <li>
        <svg viewBox="0 0 16 16" aria-hidden="true"><path d="M4 1.5 6.2 4 5 5.8c.8 1.9 2.3 3.4 4.2 4.2L11 8.8l2.5 2.2-1.2 2.6C7 13.3 2.7 9 2.4 3.7Z" fill="var(--accent)"/></svg>
        555.418.7260
      </li>
      <li>
        <svg viewBox="0 0 16 16" aria-hidden="true"><rect x="4" y="1" width="8" height="14" rx="1.5" fill="none" stroke="var(--accent)" stroke-width="1.6"/><circle cx="8" cy="12.5" r="0.9" fill="var(--accent)"/></svg>
        555.302.9914
      </li>
      <li>
        <svg viewBox="0 0 16 16" aria-hidden="true"><circle cx="8" cy="8" r="6.5" fill="none" stroke="var(--accent)" stroke-width="1.5"/><ellipse cx="8" cy="8" rx="2.8" ry="6.5" fill="none" stroke="var(--accent)" stroke-width="1.2"/><path d="M1.5 8h13" stroke="var(--accent)" stroke-width="1.2"/></svg>
        www.GuardedByVelk.example
      </li>
      <li>
        <svg viewBox="0 0 16 16" aria-hidden="true"><rect x="1.5" y="3.5" width="13" height="9" rx="1" fill="none" stroke="var(--accent)" stroke-width="1.5"/><path d="M1.5 4 8 9l6.5-5" fill="none" stroke="var(--accent)" stroke-width="1.5"/></svg>
        info@GuardedByVelk.example
      </li>
    </ul>
  </section>

</body>
</html>
```